banner for website

I need a new banner for my website. My website now is. www.brightmeadowkitchen.com, but I'm changing it to Bright Meadow Table and I need a new banner. I want me to be who it's about. I am my brand. I'm Carla Whitford. So, my name needs to be prominent in the banner along with my photo, which I'm attaching. I want my photo very prominent in the banner and very large. I am attaching my two favorites.
I need the banner plain ( with out the newsletter sign up optin part), so I can use it on my newsletters, emails and letter head, as well. I would like it to be inviting. I I have a certain color scheme I use. Deep dark brown letters with blues and greens. Very earthy and psychologically grounded. I would like to keep that color scheme. In my website banner, I need a opt in to sign up for my free monthly newsletter and receive my Free Pantry Basket Planner.

I want the shopping guide to be small and pleasant looking and to say: "Sign up to receive your Free Pantry Basket Planner and monthly newsletter."

I only want my banner to say: "Bright Meadow Table" "Carla Whitford"

I would also like to have part of the banner without the sign in for the newsletter part off of it. And also one with only the "Bright Meadow Table" and one with "Bright Meadow Table" and "Carla Whitford" without the newsletter sign up part on it either.

I hope you can do this for me. I look forward to seeing your design! Sincerely, Carla
Updates

Project Deadline Extended Reason: I couldn't view the designs so I couldn't look at the ones submitted. I just now got into the website with your company's help. I don't want to be penalized because of a problem with the log in at your site. That was not my fault. Please let me know your thoughts. Added Monday, May 9, 2016

Target Market(s)

people over 40 who have bad health or who want to learn how to be a vegetarian for better health.

Number of Pages Required

1 page

Requirements
Must have
• I want the shopping guide to be small and pleasant looking and to say: "Sign up to receive your Free Pantry Basket Planner and monthly newsletter." I would like it to blend and be elegant and not in the middle of the banner or across my face.
• I only want my banner to say: "Bright Meadow Table" "Carla Whitford"
• I would also like to have part of the banner without the sign in for the newsletter part off of it. And also one with only the "Bright Meadow Table" and one with "Bright Meadow Table" and "Carla Whitford" without the newsletter sign up part on it either.
Nice to have
• Nice font and colors. I want the background to be plants and earthy and inviting.
Should not have
• I updated and added two new photos. I think the one you were using with me in the red top looked funny under my eyes. it was too pink or something. I uploaded a better version of that photo. in hopes that it looks better. Please switch those out if you are using the one with me in the red top.

```html
<!DOCTYPE html>
<html lang="en">
<head>
<meta charset="utf-8">
<title>Bright Meadow Table – Carla Whitford</title>
<link rel="stylesheet" href="https://fonts.googleapis.com/css2?family=Abel&family=Great+Vibes&family=Merriweather:wght@300&family=Noto+Sans&family=Noto+Serif:ital,wght@0,400;0,700;1,400&family=Roboto:wght@400;700&display=swap">
<style>
  :root {
    --leaf-teal: #3fd6c8;
    --leaf-green: #4cc23a;
    --leaf-lime: #9be23c;
    --leaf-deep: #1d8a3a;
    --portrait-light: #e9dcc6;
    --portrait-warm: #c9a577;
    --bark: #4a3b2c;
    --bark-dark: #3a2e22;
    --paper: #ffffff;
    --ink: #3d3d3d;
    --ink-soft: #4b4b4b;
    --title: #4e4e4e;
    --accent-orange: #e8731a;
    --signup-yellow: #f3dc12;
    --button-top: #ffa321;
    --button-bottom: #f06a00;
    --link-green: #3f7d16;
    --brand-ink: #1f3a26;
    --name-ink: #2b2b2b;
  }
  * { box-sizing: border-box; margin: 0; padding: 0; }
  html, body { width: 1200px; height: 556px; overflow: hidden; background: var(--paper); }
  .page { position: relative; width: 1200px; height: 556px; overflow: hidden; }

  .hero {
    position: absolute; left: 0; top: 0; width: 1200px; height: 238px;
    background: linear-gradient(100deg, var(--leaf-green) 0%, var(--leaf-teal) 25%, var(--leaf-lime) 50%, var(--leaf-green) 68%, var(--leaf-deep) 78%, var(--leaf-teal) 92%, #bff3ef 100%);
  }
  .hero-portrait {
    position: absolute; left: 400px; top: 0; width: 320px; height: 238px;
    background: radial-gradient(ellipse at 50% 45%, var(--portrait-light) 0%, var(--portrait-warm) 55%, rgba(201,165,119,0) 78%);
  }

  .brand { position: absolute; left: 140px; top: 40px; display: flex; align-items: center; gap: 10px; }
  .brand-dot { width: 44px; height: 44px; border-radius: 50%; background: var(--leaf-deep); }
  .brand-name {
    font-family: "Abel", sans-serif; font-size: 25px; line-height: 24px; color: var(--brand-ink);
    width: 170px;
  }
  .owner-name {
    position: absolute; left: 196px; top: 122px;
    font-family: "Great Vibes", cursive; font-size: 50px; color: var(--name-ink);
  }

  .signup { position: absolute; left: 782px; top: 58px; width: 320px; }
  .signup-text {
    font-family: "Roboto", sans-serif; font-weight: 700; font-size: 16px; line-height: 17px;
    color: var(--signup-yellow);
  }
  .signup-form { position: absolute; left: 0; top: 55px; width: 300px; }
  .field, .signup-button {
    position: absolute; width: 146px; height: 28px; border-radius: 14px;
    font-family: "Roboto", sans-serif;
  }
  .field {
    background: var(--paper); border: 1px solid #d9d9d9; color: #8a8a8a;
    font-size: 11.5px; line-height: 26px; padding-left: 17px;
  }
  .field-first { left: 0; top: 0; }
  .field-last { left: 154px; top: 0; }
  .field-email { left: 0; top: 40px; }
  .signup-button {
    left: 154px; top: 40px; border: 2px solid #ffe2b8;
    background: linear-gradient(var(--button-top), var(--button-bottom));
    color: var(--paper); font-weight: 700; font-size: 15px; text-align: center; line-height: 24px;
  }

  .main-nav {
    position: absolute; left: 0; top: 238px; width: 1200px; height: 54px;
    background: var(--bark); box-shadow: 0 4px 10px rgba(0,0,0,0.18);
  }
  .nav-item {
    position: absolute; top: 0; height: 54px; line-height: 56px;
    font-family: "Noto Serif", serif; font-weight: 700; font-size: 13.5px; color: var(--paper);
  }
  .nav-item.is-active {
    left: 139px; top: 5px; height: 49px; line-height: 46px; width: 62px; text-align: center;
    background: var(--paper); color: var(--accent-orange); font-weight: 400; border-radius: 3px 3px 0 0;
  }

  .feature { position: absolute; top: 333px; width: 300px; }
  .feature-image { position: absolute; left: 0; top: 0; width: 100px; height: 101px; }
  .feature-body { position: absolute; left: 124px; top: 0; width: 170px; }
  .feature-title {
    font-family: "Merriweather", serif; font-weight: 300; font-size: 21px; line-height: 23px; color: var(--title);
  }
  .feature-text {
    margin-top: 13px; font-family: "Noto Sans", sans-serif; font-size: 12.8px; line-height: 20px; color: var(--ink-soft);
  }
  .feature-link {
    display: block; margin-top: 11px; font-family: "Noto Serif", serif; font-style: italic;
    font-size: 15px; color: var(--link-green); text-decoration: none;
  }
  .feature-speaker { left: 149px; }
  .feature-counsel { left: 469px; }
  .feature-books { left: 789px; }
  .image-stage { background: linear-gradient(#cfd3d6, #8c8f93); }
  .image-portrait { background: linear-gradient(135deg, #f2f2f2, #d9b3a0 50%, #b97fa0); border: 4px solid var(--paper); box-shadow: 0 2px 5px rgba(0,0,0,0.3); width: 92px; height: 86px; top: 3px; left: 4px; }
  .image-books { background: linear-gradient(160deg, #2d4a2a, #8aa35d 50%, #3a3a2a); width: 96px; height: 100px; }
</style>
</head>
<body>
<div class="page">
  <header class="hero">
    <div class="hero-portrait" role="img" aria-label="Large smiling portrait of Carla Whitford over a backdrop of translucent leaf veins"></div>
    <div class="brand">
      <span class="brand-dot"></span>
      <span class="brand-name">Bright Meadow Table</span>
    </div>
    <div class="owner-name">Carla Whitford</div>

    <div class="signup">
      <p class="signup-text">Sign up to receive your Free Pantry Basket Planner and newsletter.</p>
      <div class="signup-form">
        <div class="field field-first">First Name</div>
        <div class="field field-last">Last Name</div>
        <div class="field field-email">Email</div>
        <div class="signup-button">SIGN UP</div>
      </div>
    </div>
  </header>

  <nav class="main-nav">
    <span class="nav-item is-active">Home</span>
    <span class="nav-item" style="left:214px">Speaking »</span>
    <span class="nav-item" style="left:310px">Counseling »</span>
    <span class="nav-item" style="left:419px">Retreats &amp; Classes</span>
    <span class="nav-item" style="left:558px">Meet Carla »</span>
    <span class="nav-item" style="left:672px">Store »</span>
    <span class="nav-item" style="left:744px">Blog</span>
    <span class="nav-item" style="left:798px">References</span>
    <span class="nav-item" style="left:892px">Media</span>
  </nav>

  <section class="feature feature-speaker">
    <div class="feature-image image-stage" role="img" aria-label="Carla speaking on stage in front of a projected slide"></div>
    <div class="feature-body">
      <h2 class="feature-title">Motivational Speaker</h2>
      <p class="feature-text">Carla is a member of the Guild of Wellness Speakers, traveling internationally, employee wellness programs and ...</p>
      <a class="feature-link" href="#">Learn more</a>
    </div>
  </section>

  <section class="feature feature-counsel">
    <div class="feature-image image-portrait" role="img" aria-label="Framed photo of Carla with a microphone"></div>
    <div class="feature-body">
      <h2 class="feature-title">Nutrition Counseling</h2>
      <p class="feature-text">Whether you are looking for individualized personal health &amp; nutrition counseling, family coaching, cooking classes or a private...</p>
      <a class="feature-link" href="#">Learn more</a>
    </div>
  </section>

  <section class="feature feature-books">
    <div class="feature-image image-books" role="img" aria-label="Book and DVD covers featuring Carla with a basket of vegetables"></div>
    <div class="feature-body">
      <h2 class="feature-title">Best Nutrition, Books &amp; Products</h2>
      <p class="feature-text">Books &amp; DVD’s on nutrition &amp; healthy recipes. Food, Body Care, &amp; Home Products. Find it all here.</p>
      <a class="feature-link" href="#">Learn more</a>
    </div>
  </section>
</div>
</body>
</html>
```